Business Card: RW Office Partners - Your organised problem solver

Business Name: RW Office Partners
Website: www.rwofficepartners.com.au
Email: marisol@rwofficepartners.com.au
Mobile: 61 482 907 236
Facebook: @rwofficepartners
Instrgram: @rwofficepartners

Brading Colours:
HEX
#986474
#ddccd3
#7a8498
#c9d8e4
#000000
#ffffff

Tag Line: Your organised problem solver

Link to DRAFT website:
https://deskhelpcollective.wixsite.com/rw-office-partners

About Page from the website:
My name is Marisol Wrenfield, and I would love to assist you to become more productive in your day to day and achieve your business and personal goals.
My mission is to give you time, time to work on the important tasks of your business or to be able to spend more time with your family. I will take on the tasks you don’t have time for, don’t know well or simply don’t like to do.
I have an extensive background in Administration, Tender Coordination, Document Control, WHS and Quality Management working primarily in the Construction, Mining and Corporate World.
I am passionate about being organised, having order and making things in your life (and mine) easier! I love to watch something unfold and grow into something amazing! I am known for being the go-to problem solver, the organiser of all things, producing high standards of work even under pressure. I’m also a confident communicator, and I understand that you’re busy running your business.

Target Market(s)

Small to Medium Business who require assistance in their business by a virtual assistant.

Industry/Entity Type

Virtual Assistant

Contact Information for Business Card

Mobile: 61 482 907 236

Font styles to use
Sans Serif

Colors
ffffff

Requirements
Must have
• Branding Colours as outlined.
Contact Details as outlined.
Logo as provided.
Proper contact details - mobile, facebook, instragm, website.
Simple, Elegant, very clean looking.
Should not have
• Note cute with pictures.
Not too girly as still want to market to construction companies.

```html
<!DOCTYPE html>
<html lang="en">
<head>
<meta charset="utf-8">
<title>RW Office Partners – Business Card</title>
<link rel="stylesheet" href="https://fonts.googleapis.com/css2?family=Questrial&display=swap">
<style>
  :root {
    --mauve: #986474;
    --mauve-soft: #ddccd3;
    --slate: #7a8498;
    --mist: #c9d8e4;
    --ink: #000000;
    --paper: #ffffff;
    --backdrop: #ecedef;
  }
  * { box-sizing: border-box; margin: 0; padding: 0; }
  html, body {
    width: 1200px; height: 800px; overflow: hidden;
    background: var(--backdrop);
    font-family: "Questrial", sans-serif;
  }
  .sheet {
    width: 1200px; height: 800px;
    display: flex; align-items: center; justify-content: center; gap: 40px;
  }
  .card {
    position: relative;
    width: 560px; height: 320px;
    background: var(--paper);
    box-shadow: 0 6px 24px rgba(0,0,0,0.10);
    overflow: hidden;
  }

  /* Front */
  .card--front { display: flex; align-items: center; justify-content: center; }
  .brand-name {
    color: var(--mauve);
    font-size: 38px;
    letter-spacing: 1px;
    white-space: nowrap;
  }

  /* Back */
  .card__arcs { position: absolute; inset: 0; }
  .card__brand {
    position: absolute; left: 30px; top: 178px;
    color: var(--mauve); font-size: 19px; white-space: nowrap;
  }
  .card__title {
    position: absolute; left: 318px; top: 36px;
    color: var(--mauve); font-size: 25px; white-space: nowrap;
  }
  .contact-list {
    position: absolute; left: 318px; top: 104px;
    list-style: none;
  }
  .contact-list li {
    display: flex; align-items: center; gap: 10px;
    height: 27px; font-size: 13px; color: #3a3a3a; white-space: nowrap;
  }
  .contact-list svg { width: 15px; height: 15px; flex: none; }
  .tagline {
    position: absolute; right: 34px; bottom: 30px;
    color: var(--slate); font-size: 14px; letter-spacing: 1.5px;
  }
  .tagline__rule {
    position: absolute; right: 60px; bottom: 54px; width: 120px; height: 10px;
  }
</style>
</head>
<body>
<main class="sheet">

  <section class="card card--front" aria-label="Card front">
    <span class="brand-name">RW Office Partners</span>
  </section>

  <section class="card card--back" aria-label="Card back">
    <svg class="card__arcs" viewBox="0 0 560 320" aria-hidden="true">
      <path d="M212 -4 C 300 70, 300 230, 226 324" fill="none" stroke="var(--mist)" stroke-width="6"/>
      <path d="M236 -4 C 330 70, 326 240, 244 324" fill="none" stroke="var(--mauve)" stroke-width="5"/>
    </svg>

    <span class="card__brand">RW Office Partners</span>
    <h1 class="card__title" style="font-weight:400">RW Office Partners</h1>

    <ul class="contact-list">
      <li>
        <svg viewBox="0 0 16 16"><rect x="1" y="3" width="14" height="10" fill="var(--mauve)"/><path d="M1 3 L8 9 L15 3" fill="none" stroke="var(--paper)" stroke-width="1.2"/></svg>
        marisol@rwofficepartners.com.au
      </li>
      <li>
        <svg viewBox="0 0 16 16"><circle cx="8" cy="8" r="6.5" fill="none" stroke="var(--mauve)" stroke-width="1.4"/><ellipse cx="8" cy="8" rx="3" ry="6.5" fill="none" stroke="var(--mauve)" stroke-width="1.2"/><line x1="1.5" y1="8" x2="14.5" y2="8" stroke="var(--mauve)" stroke-width="1.2"/></svg>
        www.rwofficepartners.com.au
      </li>
      <li>
        <svg viewBox="0 0 16 16"><circle cx="8" cy="8" r="6" fill="var(--mauve)"/></svg>
        @rwofficepartners
      </li>
      <li>
        <svg viewBox="0 0 16 16"><rect x="2" y="2" width="12" height="12" fill="var(--mauve)"/></svg>
        @rwofficepartners
      </li>
      <li>
        <svg viewBox="0 0 16 16"><path d="M4 1.5 L6.5 1.5 L7.5 5 L5.8 6.2 C6.6 8 8 9.4 9.8 10.2 L11 8.5 L14.5 9.5 L14.5 12 C14.5 13.5 13 14.5 11.5 14.2 C6.5 13 3 9.5 1.8 4.5 C1.5 3 2.5 1.5 4 1.5 Z" fill="var(--mauve)"/></svg>
        61 482 907 236
      </li>
    </ul>

    <svg class="tagline__rule" viewBox="0 0 120 10" aria-hidden="true">
      <path d="M0 9 Q 60 4 120 1" fill="none" stroke="var(--slate)" stroke-width="1"/>
    </svg>
    <p class="tagline">Your organised problem solver</p>
  </section>

</main>
</body>
</html>
```